Accounting firm needing business card / letterhead designed
Marcus L. Trenholm, CPA
marcus@veltrowledger.com
www.veltrowledger.com
842 E Alder Ave Brookvale, WA 43827
555-562-0974

```html
<!DOCTYPE html>
<html lang="en">
<head>
<meta charset="utf-8">
<title>Veltro Ledger – Business Card</title>
<link rel="stylesheet" href="https://fonts.googleapis.com/css2?family=Roboto:wght@400;500&family=Roboto+Condensed:wght@500&display=swap">
<style>
  :root {
    --navy: #262262;
    --green: #84bd3a;
    --paper: #f4f4f4;
    --white: #ffffff;
    --backdrop: #e6e4e0;
  }
  * { margin: 0; padding: 0; box-sizing: border-box; }
  html, body { width: 1200px; height: 960px; overflow: hidden; }
  body {
    position: relative;
    background: var(--backdrop);
    font-family: "Roboto", Arial, sans-serif;
  }
  .card {
    position: absolute;
    width: 600px;
    height: 343px;
    overflow: hidden;
    box-shadow: 0 2px 5px rgba(0,0,0,0.25);
  }

  /* Contact side */
  .card--contact { left: 314px; top: 113px; background: var(--paper); }
  .card__brand {
    position: absolute;
    top: 78px; left: 0; width: 100%;
    text-align: center;
    font-weight: 500;
    font-size: 44px;
    line-height: 52px;
    letter-spacing: 4px;
    color: var(--navy);
  }
  .card__band {
    position: absolute;
    left: 0; top: 207px;
    width: 600px; height: 136px;
    background: var(--navy);
  }
  .card__divider { position: absolute; left: 0; top: 203px; }
  .holder {
    position: absolute;
    left: 39px; top: 243px;
    color: var(--white);
  }
  .holder__name {
    font-family: "Roboto Condensed", Arial, sans-serif;
    font-weight: 500;
    font-size: 21px;
    margin-bottom: 6px;
  }
  .holder__address { font-size: 14.5px; line-height: 18px; }
  .contact-list {
    position: absolute;
    right: 39px; top: 252px;
    list-style: none;
    color: var(--white);
    font-size: 14.5px;
    line-height: 19px;
    text-align: right;
  }
  .contact-list li { display: flex; justify-content: flex-end; align-items: center; gap: 7px; }
  .contact-list svg { width: 12px; height: 12px; fill: var(--white); }

  /* Brand side */
  .card--brand { left: 311px; top: 472px; background: var(--green); }
  .card--brand .card__brand {
    top: 138px;
    color: var(--white);
    font-size: 46px;
  }
  .card__web {
    position: absolute;
    left: 0; top: 280px; width: 100%;
    text-align: center;
    color: var(--white);
    font-size: 14px;
    letter-spacing: 6.5px;
  }
</style>
</head>
<body>

  <section class="card card--contact" aria-label="Business card, contact side">
    <div class="card__brand">VELTRO LEDGER</div>
    <div class="card__band"></div>
    <svg class="card__divider" width="600" height="24" viewBox="0 0 600 24" aria-hidden="true">
      <polygon points="0,4 489,4 498,21 507,4 600,4 600,24 0,24" fill="var(--navy)"/>
      <polyline points="0,5 489,5 498,21 507,5 600,5" fill="none" stroke="var(--green)" stroke-width="3"/>
    </svg>
    <div class="holder">
      <div class="holder__name">Marcus L. Trenholm, CPA</div>
      <div class="holder__address">842 E Alder Ave<br>Brookvale, WA 43827</div>
    </div>
    <ul class="contact-list">
      <li>555-562-0974
        <svg viewBox="0 0 24 24" aria-hidden="true"><path d="M6.6 10.8a15.1 15.1 0 0 0 6.6 6.6l2.2-2.2a1 1 0 0 1 1-.25 11.4 11.4 0 0 0 3.6.57 1 1 0 0 1 1 1V20a1 1 0 0 1-1 1A17 17 0 0 1 3 4a1 1 0 0 1 1-1h3.5a1 1 0 0 1 1 1c0 1.25.2 2.45.57 3.57a1 1 0 0 1-.25 1z"/></svg>
      </li>
      <li>marcus@veltrowledger.com
        <svg viewBox="0 0 24 24" aria-hidden="true"><path d="M2 5h20v14H2z M2 5l10 8 10-8" fill="var(--white)" stroke="var(--navy)" stroke-width="1.5"/></svg>
      </li>
      <li>www.veltrowledger.com
        <svg viewBox="0 0 24 24" aria-hidden="true"><circle cx="12" cy="12" r="11"/><path d="M1 12h22M12 1c4 4 4 18 0 22M12 1c-4 4-4 18 0 22" fill="none" stroke="var(--navy)" stroke-width="1.5"/></svg>
      </li>
    </ul>
  </section>

  <section class="card card--brand" aria-label="Business card, brand side">
    <div class="card__brand">VELTRO LEDGER</div>
    <div class="card__web">www.veltrowledger.com</div>
  </section>

</body>
</html>
```